Web Design job - NetKestrel Company including Desktop & Mobile version

Create a Web Design (Uncoded - PSD layout only)

1. About our company

NetKestrel is an Australian-based company which sells used networking devices to coporates and other brokers in USA, Europe and other countries. We are the market leader in this space and currently have warehouses in Sydney and California. Most of our products are from VORLAN.

Our competitive advantages come from lowest price in the market, flexible product configuration for different demands of customers, long time experience in the business and huge stock of inventory.

We are in need of a new website to enhance customer and partner engagement which are measured by sales metrics and website performance metrics such as number of request for a quote, number of new orders, return visits, views, conversion rate, etc.

2. Website structure:

We need different looks for different devices: Desktop, iPad and Mobile with popular screen resolutions for each of following page.

Try to make one as good as possible, then we can move further. Below are the main pages of the web:

+ Home Page: Where customers learn about the company and its business. Should have: Beautiful company profile, highlighted company contact and strengths; A comprehensive overview about selling products.

+ Category Page: Where customers learn about products in a category and do the search action. Should focus on filter and sort functions for easily finding a product.

+ Product Page: Where customers learn about the details of a specific products such as price, image, description, related products.
- Also need features for cross-sell or up-sell.
- An item may have both new and refurbished prices, or either or none of them. Should have options to choose between new or refurbished price to add to cart.

+ Information Page: About the company, Company Announcement.

+ Cart management and Check-out

+ Search results

REFERENCES
Current website: http://netkestrel.com.au/

Prefered Layout:
- https://www.gearbazaar-example.com/en/vorlan-systems/vorlan-router-series/vorlan-series-1900/vorlan-systems-vorlan1941-k9
- https://www.wiresandboxes-example.com/vorlan-2port-rj48-multiflex-t1-trunk-card-vwic2mftt1-p-1374.html
- The attached files play as wireframes, only for the purpose of guiding. You are free to make your choices of colors and layouts.

Target Market(s)

- Corporate clients
- Main market: Australia

Industry/Entity Type

It Company

Number of Pages Required

3 page

Font styles to use
Sans Serif

Requirements
Must have
• - The new design should have a clear look to easily find information while should look professional to aim at corporate clients.
• - Require least time or effort to finish a task
• - Optimize for SEO and loading time
• - Mobile version is optimized for touching, swiping and loading time.
• - Bear in mind that the new website need minimum effort of manual tasks such as updating content. We don’t have human resources for these yet.
Nice to have
• - Should have design for each scenario such as click, popup, dropdown, deactive, have/not have an object

```html
<!DOCTYPE html>
<html lang="en">
<head>
<meta charset="utf-8">
<title>NetKestrel – Networking Equipment</title>
<link href="https://fonts.googleapis.com/css2?family=Open+Sans:wght@400;600;700;800&display=swap" rel="stylesheet">
<style>
:root{
  --blue:#0b4ea2;
  --orange:#dc6d2c;
  --orange-light:#eba270;
  --orange-deep:#c55f22;
  --yellow:#f4b31a;
  --text:#333;
  --muted:#666;
  --grey-bg:#f4f4f4;
  --footer:#2b2b2b;
  --footer-text:#9a9a9a;
  --red:#e0302b;
}
*{box-sizing:border-box;margin:0;padding:0}
html,body{width:1200px;height:2273px;overflow:hidden}
body{font-family:"Open Sans",Arial,sans-serif;color:var(--text);background:#fff;position:relative}
.wrap{width:936px;margin:0 auto;position:relative}
svg.i{display:inline-block;vertical-align:middle;fill:currentColor}

/* header */
.site-header{height:115px}
.site-header .wrap{display:flex;align-items:center;height:115px}
.brand{display:flex;align-items:center;gap:10px;width:270px}
.brand-dot{width:40px;height:40px;border-radius:50%;background:var(--blue)}
.brand-name{font-size:30px;font-weight:700;color:var(--blue)}
.search{width:244px;height:40px;border:1px solid #c8c8c8;display:flex;align-items:center;justify-content:space-between;padding:0 14px;font-size:12px;color:#666}
.contact-mini{margin-left:auto;text-align:right;font-size:13px;line-height:1.4}
.contact-mini .phone{font-size:17px}
.cart{width:40px;height:40px;border-radius:50%;background:var(--blue);color:#fff;margin-left:14px;display:flex;flex-direction:column;align-items:center;justify-content:center;font-size:10px;line-height:1.1}
.quote-btn{margin-left:12px;background:var(--blue);color:#fff;font-size:14px;height:40px;width:143px;display:flex;align-items:center;justify-content:center;gap:7px}

/* nav */
.main-nav{background:var(--orange);height:40px}
.main-nav ul{list-style:none;display:flex;height:40px}
.main-nav li{width:156px;text-align:center;color:#fff;font-size:15px;font-weight:600;line-height:40px;text-transform:uppercase}
.main-nav li.active{background:var(--orange-deep);width:122px}

/* hero */
.hero{height:459px;background:linear-gradient(110deg,#3c3f45 0%,#1f232a 40%,#2a3440 65%,#141a22 100%);position:relative;text-align:center;color:#fff}
.hero-title{position:absolute;top:154px;left:0;right:0;font-size:48px;font-weight:800;letter-spacing:0.5px}
.hero-sub{position:absolute;top:210px;left:0;right:0;font-size:20px}
.hero-btn{position:absolute;top:246px;left:528px;width:144px;height:48px;background:var(--yellow);color:#1d1d1d;font-weight:700;font-size:19px;line-height:48px}
.hero-arrow{position:absolute;top:366px;width:24px;height:32px;background:rgba(0,0,0,.5);color:#fff;display:flex;align-items:center;justify-content:center}
.hero-arrow.left{left:0}.hero-arrow.right{right:0}

/* categories */
.section-title{color:var(--blue);font-size:24px;font-weight:700;text-align:center;text-transform:uppercase}
.categories{padding-top:76px}
.cat-tiles{display:flex;gap:3px;margin-top:20px}
.cat-tile{width:232px;height:176px;background:var(--blue);color:#fff;text-align:center;position:relative;font-size:16px}
.cat-tile.active{background:var(--orange)}
.cat-tile.active::after{content:"";position:absolute;left:104px;bottom:-15px;border:14px solid transparent;border-top-color:var(--orange);border-bottom:0}
.cat-icon{width:96px;height:96px;border-radius:50%;background:#fff;margin:24px auto 14px;display:flex;align-items:center;justify-content:center}
.cat-icon span{width:58px;height:38px;border-radius:4px;background:linear-gradient(#777,#2d2d2d)}

.product-area{display:flex;margin-top:36px}
.filter-list{width:175px;height:252px;background:#ececec;list-style:none}
.filter-list li{height:38px;border-bottom:1px solid #d8d8d8;padding:0 14px;font-size:13px;display:flex;justify-content:space-between;align-items:center;background:#f2f2f2}
.filter-list li.active{color:var(--blue)}
.products{display:flex;gap:13px;margin-left:14px}
.product{width:176px}
.product-img{height:160px;border:1px solid #c8c8c8;display:flex;align-items:center;justify-content:center}
.product-img span{width:110px;height:60px;border-radius:6px;background:linear-gradient(#d8d8d8,#4a4a4a)}
.product-name{text-align:center;font-size:13px;margin:10px 0 8px}
.price-row{display:flex;justify-content:space-between;font-size:11px;color:var(--muted);line-height:19px}
.price-row b{color:var(--red);font-weight:400}
.save{font-size:11px;color:var(--muted);line-height:21px}

/* welcome */
.welcome{position:absolute;top:1273px;left:0;width:1200px;height:383px;background:var(--grey-bg);text-align:center}
.welcome .section-title{margin-top:51px}
.welcome p{font-size:13.4px;line-height:23px;color:#444;width:950px;margin:14px auto 0}
.welcome .brands{color:var(--blue);font-size:14px}
.stats{display:flex;width:980px;margin:18px auto 0}
.stat{flex:1}
.stat strong{display:block;font-size:32px;font-weight:700;color:#3b3b3b}
.stat span{display:block;font-size:13px;text-transform:uppercase;line-height:17px;margin-top:3px}
.read-more{display:inline-block;margin-top:24px;border:1px solid #d0d0d0;background:#fff;font-size:12px;color:#555;width:96px;height:40px;line-height:38px}

/* quote */
.quote{position:absolute;top:1656px;left:0;width:1200px;height:188px;text-align:center}
.quote .section-title{margin-top:43px}
.quote p{font-size:14px;margin-top:10px}
.quote-contacts{margin-top:10px;font-size:25px;display:flex;justify-content:center;gap:30px}

/* info strip */
.info-strip{position:absolute;top:1844px;left:0;width:1200px;height:65px;background:var(--orange-light)}
.info-strip .wrap{display:flex;gap:6px;height:65px}
.info-strip a{flex:1;background:var(--orange);color:#fff;font-size:24px;font-weight:600;display:flex;align-items:center;justify-content:center;gap:12px;text-decoration:none}
.info-strip::before,.info-strip::after{content:"";position:absolute;top:0;bottom:0;width:6px;background:#fff}
.info-strip::before{left:126px}.info-strip::after{right:126px}

/* footer */
.site-footer{position:absolute;top:1912px;left:0;width:1200px;height:259px;background:var(--footer);color:var(--footer-text)}
.footer-cols{display:flex;padding-top:44px}
.footer-cols h4{color:#eee;font-weight:400;font-size:17px;margin-bottom:14px;white-space:nowrap}
.col-about{width:210px;margin-right:32px;font-size:11px;line-height:21px}
.col-contact{width:309px}
.col-contact li{list-style:none;font-size:11px;line-height:28px;display:flex;gap:14px;align-items:center;white-space:nowrap}
.col-contact li svg{width:10px;flex:none}
.col-pay{width:192px}
.pay-row{display:flex;gap:10px}
.pay-row span{width:26px;height:16px;background:#777;border-radius:2px}
.col-why{width:200px}
.col-why li{list-style:none;color:#eee;font-size:13px;line-height:29px;display:flex;gap:10px;align-items:center;white-space:nowrap}
.footer-bottom{position:absolute;top:2171px;left:0;width:1200px;height:102px;background:var(--footer);border-top:1px solid #3a3a3a;color:var(--footer-text);font-size:11px}
.footer-bottom .links{position:absolute;top:28px;left:132px}
.footer-bottom .copy{position:absolute;top:54px;left:132px}
.social{position:absolute;top:38px;left:1008px;display:flex;gap:6px}
.social span{width:25px;height:25px;border-radius:50%;background:#3b5998}
.social span+span{background:#1da1f2}
</style>
</head>
<body>

<header class="site-header">
  <div class="wrap">
    <div class="brand"><span class="brand-dot"></span><span class="brand-name">NetKestrel</span></div>
    <div class="search">Search
      <svg class="i" width="15" height="15" viewBox="0 0 16 16"><circle cx="6.5" cy="6.5" r="5" fill="none" stroke="#555" stroke-width="2"/><path d="M10 10l5 5" stroke="#555" stroke-width="2.4"/></svg>
    </div>
    <div class="contact-mini">
      <div><svg class="i" width="11" height="9" viewBox="0 0 12 9"><path d="M0 0h12v9H0z"/><path d="M0 0l6 5 6-5" fill="none" stroke="#fff"/></svg> hello@netkestrel-example.com</div>
      <div class="phone"><svg class="i" width="14" height="14" viewBox="0 0 16 16"><path d="M3 1l3 0 1 4-2 1.5c1 2 2.5 3.5 4.5 4.5L11 9l4 1v3c0 1-1 2-2 2C7 15 1 9 1 3c0-1 1-2 2-2z"/></svg> (+61) 02 5550 1234</div>
    </div>
    <div class="cart">0<svg class="i" width="12" height="11" viewBox="0 0 14 12"><path d="M0 0h3l1 2h10l-2 6H5zM5 10a1 1 0 100 2 1 1 0 000-2zm6 0a1 1 0 100 2 1 1 0 000-2z"/></svg></div>
    <div class="quote-btn"><svg class="i" width="14" height="14" viewBox="0 0 16 16"><path d="M1 3h8v2H3v8h8V9h2v6H1zM12 1l3 3-7 7H5V8z"/></svg>Request a Quote</div>
  </div>
</header>

<nav class="main-nav">
  <ul class="wrap">
    <li class="active">Home</li><li>Routers</li><li>Switches</li><li>Wirelesses</li><li>IP Phones</li><li>Accessories</li>
  </ul>
</nav>

<section class="hero" role="img" aria-label="Photo of server racks with networking equipment in a data centre">
  <div class="hero-title">SAVE UP TO 40%</div>
  <div class="hero-sub">By doing business with NetKestrel</div>
  <div class="hero-btn">STOCK LIST</div>
  <div class="hero-arrow left"><svg class="i" width="8" height="14" viewBox="0 0 8 14"><path d="M7 1L1 7l6 6" fill="none" stroke="#fff" stroke-width="1.5"/></svg></div>
  <div class="hero-arrow right"><svg class="i" width="8" height="14" viewBox="0 0 8 14"><path d="M1 1l6 6-6 6" fill="none" stroke="#fff" stroke-width="1.5"/></svg></div>
</section>

<section class="categories wrap">
  <h2 class="section-title">Product Categories</h2>
  <div class="cat-tiles">
    <div class="cat-tile active"><div class="cat-icon"><span role="img" aria-label="Wireless access points and security appliance"></span></div>Wireless &amp; Securities</div>
    <div class="cat-tile"><div class="cat-icon"><span role="img" aria-label="Router and switch units"></span></div>Routers &amp; Switches</div>
    <div class="cat-tile"><div class="cat-icon"><span role="img" aria-label="Desk IP phones"></span></div>IP Phones</div>
    <div class="cat-tile"><div class="cat-icon"><span role="img" aria-label="Transceiver modules and cables"></span></div>Accessories</div>
  </div>

  <div class="product-area">
    <ul class="filter-list">
      <li class="active">Best Price<span>›</span></li>
      <li>Most Sale<span>›</span></li>
      <li>New Products<span>›</span></li>
      <li>In Promotion<span>›</span></li>
    </ul>
    <div class="products">
      <div class="product"><div class="product-img"><span role="img" aria-label="Wireless access point"></span></div><div class="product-name">NKX-WAVE310-Q5</div><div class="price-row">New<b>A$520</b></div><div class="price-row">Referbished<b>A$220</b></div><div class="save">(Save : $A300 - 30%)</div></div>
      <div class="product"><div class="product-img"><span role="img" aria-label="Rack router"></span></div><div class="product-name">NKX-WAVE310-Q5</div><div class="price-row">New<b>A$520</b></div><div class="price-row">Referbished<b>A$220</b></div><div class="save">(Save : $A300 - 30%)</div></div>
      <div class="product"><div class="product-img"><span role="img" aria-label="Desktop router"></span></div><div class="product-name">NKX-WAVE310-Q5</div><div class="price-row">New<b>A$520</b></div><div class="price-row">Referbished<b>A$220</b></div><div class="save">(Save : $A300 - 30%)</div></div>
      <div class="product"><div class="product-img"><span role="img" aria-label="Rack-mount router"></span></div><div class="product-name">NKX-WAVE310-Q5</div><div class="price-row">New<b>A$520</b></div><div class="price-row">Referbished<b>A$220</b></div><div class="save">(Save : $A300 - 30%)</div></div>
    </div>
  </div>
</section>

<section class="welcome">
  <h2 class="section-title">Welcome to NetKestrel</h2>
  <p>With over fifteen years experience selling and buying new and used networking equipment, NetKestrel is one of the most preeminent and longest established businesses in the global reseller marketplace. The manufacturers that we specialise in include;<br><span class="brands">VORLAN, Junova (New Products Only), Nortrex, Avelio, HQ Systems, 4Link, Forgeway, Entrivo, Brocanta and Packetline.</span></p>
  <div class="stats">
    <div class="stat"><strong>7</strong><span>Years of experience</span></div>
    <div class="stat"><strong>99.5%</strong><span>Positive feedback on AuctionHub</span></div>
    <div class="stat"><strong>300</strong><span>Clients &amp; partners around<br>the world</span></div>
    <div class="stat"><strong>1.250</strong><span>SKUs in inventory</span></div>
  </div>
  <span class="read-more">Read more</span>
</section>

<section class="quote">
  <h2 class="section-title">Request a Quote</h2>
  <p>Call today for a great price on new and used networking equipment Or email</p>
  <div class="quote-contacts">
    <span><svg class="i" width="20" height="20" viewBox="0 0 16 16"><path d="M3 1l3 0 1 4-2 1.5c1 2 2.5 3.5 4.5 4.5L11 9l4 1v3c0 1-1 2-2 2C7 15 1 9 1 3c0-1 1-2 2-2z"/></svg> (061) 02 5550 1234</span>
    <span><svg class="i" width="22" height="17" viewBox="0 0 12 9"><path d="M0 0h12v9H0z"/><path d="M0 0l6 5 6-5" fill="none" stroke="#fff"/></svg> hello@netkestrel-example.com</span>
  </div>
</section>

<section class="info-strip">
  <div class="wrap">
    <a><svg class="i" width="20" height="20" viewBox="0 0 20 20"><circle cx="10" cy="10" r="8.5" fill="none" stroke="#fff" stroke-width="2"/><path d="M5 10h9M10 6l4 4-4 4" fill="none" stroke="#fff" stroke-width="2"/></svg>Warranty</a>
    <a><svg class="i" width="20" height="20" viewBox="0 0 20 20"><circle cx="10" cy="10" r="8.5" fill="none" stroke="#fff" stroke-width="2"/><path d="M5 10h9M10 6l4 4-4 4" fill="none" stroke="#fff" stroke-width="2"/></svg>Privacy Statment</a>
    <a><svg class="i" width="20" height="20" viewBox="0 0 20 20"><circle cx="10" cy="10" r="8.5" fill="none" stroke="#fff" stroke-width="2"/><path d="M5 10h9M10 6l4 4-4 4" fill="none" stroke="#fff" stroke-width="2"/></svg>Terms of Trade</a>
  </div>
</section>

<footer class="site-footer">
  <div class="wrap footer-cols">
    <div class="col-about"><h4>About Us</h4>Pellentesque magna orci, placerat at nisl at, porta ultrices turpis. Fusce in eros non orci posuere viverra ut a lectus. In mattis, lorem sit amet consequat placerat, augue nulla mollis turpis, vitae egestas est tellus in nulla. Vestibulum convallis rutrum tincidunt. Aenean sit amet suscipit leo.</div>
    <div class="col-contact"><h4>Contact Us</h4>
      <ul>
        <li><svg class="i" viewBox="0 0 10 14" height="12"><path d="M5 0a5 5 0 00-5 5c0 4 5 9 5 9s5-5 5-9a5 5 0 00-5-5z"/></svg>Unit 9/12 Harbour Lane Rydalmere, NSW 2116</li>
        <li><svg class="i" viewBox="0 0 16 16" height="11"><path d="M3 1l3 0 1 4-2 1.5c1 2 2.5 3.5 4.5 4.5L11 9l4 1v3c0 1-1 2-2 2C7 15 1 9 1 3c0-1 1-2 2-2z"/></svg>(+61)2 5550 1234/ 04 5550 7788</li>
        <li><svg class="i" viewBox="0 0 16 16" height="11"><circle cx="8" cy="8" r="6.5" fill="none" stroke="currentColor" stroke-width="2"/><path d="M8 4v4h3" fill="none" stroke="currentColor" stroke-width="2"/></svg>8.30 am - 5.30 pm / Mon - Fri (UTC + 10)</li>
        <li><svg class="i" viewBox="0 0 12 9" height="9"><path d="M0 0h12v9H0z"/></svg>sales@netkestrel.com.au</li>
        <li><svg class="i" viewBox="0 0 16 16" height="11"><circle cx="8" cy="8" r="7"/></svg>http://stores.auctionhub-example.com.au/netkestrel/</li>
      </ul>
    </div>
    <div class="col-pay"><h4>Payment Methods</h4><div class="pay-row"><span></span><span></span><span></span></div></div>
    <div class="col-why"><h4>Why us</h4>
      <ul>
        <li><svg class="i" width="10" height="14" viewBox="0 0 10 14"><text x="1" y="12" font-size="14" fill="#eee" font-family="Open Sans, sans-serif">$</text></svg>100% wholesale price</li>
        <li><svg class="i" width="12" height="12" viewBox="0 0 12 12"><circle cx="6" cy="6" r="5" fill="#eee"/></svg>100% quality assurance</li>
        <li><svg class="i" width="12" height="12" viewBox="0 0 12 12"><path d="M1 8V6a5 5 0 0110 0v2" fill="none" stroke="#eee" stroke-width="1.6"/><rect x="0" y="7" width="3" height="4" fill="#eee"/><rect x="9" y="7" width="3" height="4" fill="#eee"/></svg>Free support</li>
        <li><svg class="i" width="12" height="12" viewBox="0 0 12 12"><path d="M10 6a4 4 0 11-1.2-2.8" fill="none" stroke="#eee" stroke-width="1.8"/><path d="M7 1h4v4z" fill="#eee"/></svg>100% money back guarantee</li>
        <li><svg class="i" width="11" height="12" viewBox="0 0 11 12"><path d="M5.5 0L11 2v4c0 3-2.5 5-5.5 6C2.5 11 0 9 0 6V2z" fill="#eee"/></svg>Flexible payment</li>
      </ul>
    </div>
  </div>
</footer>

<div class="footer-bottom">
  <div class="links">Home &nbsp;|&nbsp; Routers &nbsp;|&nbsp; Switches &nbsp;|&nbsp; Wirelesses &nbsp;|&nbsp; IP Phones &nbsp;|&nbsp; Accessories</div>
  <div class="copy">Copyright © 2017 &nbsp;NetKestrel Pty Ltd. &nbsp;All rights reserved.</div>
  <div class="social"><span></span><span></span></div>
</div>

</body>
</html>
```